Internet Service Tech provider product flyer redesign - High Rise WIFI

We have created the attached flyer in Word and also attached a PDF. All the content is correct. We just need a complete re-design of the flyer with new relevant hi-res images (based on content) and a more streamlined/cleaner layout.

This product is an entire in-building WIFI system for Body's Corporate in High Rise buildings.

We are a Brisbane-based internet tech company that specialises in providing solutions for High Rise buildings

Body text style - Helvetica Light

Internet

```html
<!DOCTYPE html>
<html lang="en">
<head>
<meta charset="utf-8">
<title>High-Rise WIFI Flyer</title>
<link rel="stylesheet" href="https://fonts.googleapis.com/css2?family=Archivo+Black&family=Roboto:wght@300;400&family=Roboto+Condensed:wght@300;400;700&display=swap">
<style>
  :root {
    --navy: #0b2329;
    --teal: #2f5f70;
    --sky-top: #2e6fb8;
    --sky-mid: #8fb8dc;
    --sky-light: #dfeaf4;
    --orb-light: #3f86d0;
    --orb-dark: #123f78;
    --accent-blue: #1f6fb4;
    --link-blue: #2f86cf;
    --ink: #2a2a2a;
    --white: #ffffff;
  }
  html, body { margin: 0; padding: 0; overflow: hidden; background: #ffffff; }
  .flyer {
    position: relative; width: 848px; height: 1200px; overflow: hidden;
    background: var(--white);
    font-family: "Roboto", Helvetica, Arial, sans-serif;
  }
  .backdrop { position: absolute; inset: 0; }
  .stat-orb {
    position: absolute; left: 359px; top: 186px; width: 280px; height: 240px;
    display: flex; align-items: center; justify-content: center; text-align: center;
    white-space: nowrap;
    font-family: "Roboto Condensed", sans-serif; font-weight: 700; font-size: 24px;
    line-height: 37px; letter-spacing: 0.4px; color: var(--white); text-transform: uppercase;
  }
  .intro { position: absolute; left: 50px; top: 472px; width: 445px; }
  .intro-heading {
    margin: 0 0 48px; font-family: "Archivo Black", sans-serif; font-weight: 400;
    font-size: 23px; line-height: 30px; color: var(--navy);
  }
  .intro p {
    margin: 0 0 13px; font-weight: 300; font-size: 15.3px; line-height: 19.5px; color: var(--ink);
  }
  .pull-quote {
    position: absolute; left: 250px; top: 800px; width: 244px; margin: 0; text-align: right;
    font-family: "Roboto Condensed", sans-serif; font-weight: 300; font-size: 21px;
    line-height: 25px; color: var(--ink);
  }
  .benefit { position: absolute; left: 558px; width: 266px; }
  .benefit-title {
    display: flex; align-items: center; gap: 6px; margin: 0 0 5px;
    font-family: "Roboto Condensed", sans-serif; font-weight: 700; font-size: 19px;
    color: var(--navy); text-transform: uppercase;
  }
  .benefit-title svg { width: 22px; height: 24px; flex: none; }
  .benefit p {
    margin: 0 0 0 14px; font-weight: 400; font-size: 12.6px; line-height: 16px;
    color: var(--white); text-align: justify;
  }
  .benefit--demand { top: 470px; }
  .benefit--managed { top: 610px; }
  .benefit--value { top: 744px; }
  .contact { position: absolute; left: 64px; top: 978px; color: var(--white); }
  .contact-heading {
    margin: 0 0 16px; font-family: "Roboto Condensed", sans-serif; font-weight: 700;
    font-size: 30px; color: var(--accent-blue); letter-spacing: 0.3px;
  }
  .contact-lines {
    margin: 0 0 16px; font-family: "Roboto Condensed", sans-serif; font-size: 14.5px; line-height: 20px;
  }
  .contact-web {
    margin: 0; font-family: "Roboto Condensed", sans-serif; font-size: 15px;
    line-height: 21px; color: var(--link-blue);
  }
</style>
</head>
<body>
<div class="flyer">
  <svg class="backdrop" width="848" height="1200" viewBox="0 0 848 1200" aria-hidden="true">
    <defs>
      <linearGradient id="skyLeft" x1="0" y1="0" x2="1" y2="1">
        <stop offset="0" stop-color="var(--sky-light)"/>
        <stop offset="0.45" stop-color="var(--sky-mid)"/>
        <stop offset="1" stop-color="var(--sky-top)"/>
      </linearGradient>
      <linearGradient id="skyRight" x1="1" y1="0" x2="0" y2="1">
        <stop offset="0" stop-color="var(--sky-light)"/>
        <stop offset="0.5" stop-color="var(--sky-mid)"/>
        <stop offset="1" stop-color="var(--sky-top)"/>
      </linearGradient>
      <radialGradient id="orb" cx="0.45" cy="0.3" r="0.8">
        <stop offset="0" stop-color="var(--orb-light)"/>
        <stop offset="1" stop-color="var(--orb-dark)"/>
      </radialGradient>
    </defs>
    <path role="img" aria-label="Photo of a curved glass office tower against the sky" fill="url(#skyLeft)"
      d="M0,0 L518,0 C508,110 480,190 440,250 C330,250 150,220 0,150 Z"/>
    <path fill="var(--navy)" d="M0,150 C150,220 330,250 440,250 L430,300 C300,300 130,265 0,212 Z"/>
    <path role="img" aria-label="Photo of a glass high-rise facade reaching into blue sky" fill="url(#skyRight)"
      d="M552,0 L848,0 L848,150 C760,220 680,262 600,284 C578,200 560,100 552,0 Z"/>
    <path fill="var(--navy)" d="M600,284 C680,262 760,220 848,150 L848,206 C760,268 690,305 612,330 Z"/>
    <path fill="var(--navy)" d="M0,936 C250,926 450,944 660,990 L660,1200 L0,1200 Z"/>
    <path fill="var(--teal)" d="M848,206 C760,268 690,305 612,330 C560,370 528,420 528,480 L534,720 C545,860 610,1010 712,1200 L848,1200 Z"/>
    <circle cx="499" cy="306" r="131" fill="var(--white)"/>
    <circle cx="499" cy="306" r="120" fill="url(#orb)"/>
  </svg>

  <div class="stat-orb">On average, every<br>Australian has 2.6*<br>wireless devices.</div>

  <section class="intro">
    <h1 class="intro-heading">Why Body’s Corporate need to provide High-Rise WIFI?</h1>
    <p>The demand and consumption of digital content and the way it is delivered to tenants, owners, guests, and consumers is increasing exponentially every day. This massive increase in digital demand means Body’s Corporate need to ensure that their buildings Communication, Internet and WIFI infrastructure is upgraded properly to cater for such mass amounts of digital demand by residents.</p>
    <p>We can help Body’s Corporate plan, project manage and bulk supply all aspects of upgrading and implementing a High-Rise WIFI build that is designed from the ground up for high-rise buildings.</p>
  </section>

  <blockquote class="pull-quote">“Internet is now considered by many as a utility, just like water, gas and electricity”</blockquote>

  <section class="benefit benefit--demand">
    <h2 class="benefit-title">
      <svg viewBox="0 0 22 24" aria-hidden="true"><circle cx="8" cy="2.5" r="1.6" fill="var(--navy)"/><circle cx="12" cy="5" r="1.2" fill="var(--navy)"/><path d="M8,8 H14 V12 L20,22 H2 L8,12 Z" fill="var(--navy)"/></svg>
      Meet resident demand
    </h2>
    <p>Ensure that your building/s residents have access to proper digital connectivity, Fibre-type speed Internet, and HD WIFI using a bulk supply service that is scalable with future usage and growth</p>
  </section>

  <section class="benefit benefit--managed">
    <h2 class="benefit-title">
      <svg viewBox="0 0 22 24" aria-hidden="true"><g fill="none" stroke="var(--navy)" stroke-width="3" stroke-linecap="round"><path d="M9,15 L5,19 A3,3 0 0 1 1,15 L6,10 A3,3 0 0 1 10,10"/><path d="M13,9 L17,5 A3,3 0 0 1 21,9 L16,14 A3,3 0 0 1 12,14"/><path d="M8,16 L14,8"/></g></svg>
      Fully managed service
    </h2>
    <p>Our connected community platform is a complete managed service which helps minimize a Body’s Corporate involvement in the day-to-day operations, and resident billing of the services</p>
  </section>

  <section class="benefit benefit--value">
    <h2 class="benefit-title">
      <svg viewBox="0 0 22 24" aria-hidden="true"><path d="M3,21 C3,10 10,4 20,3 C20,13 14,20 5,20 Z" fill="var(--navy)"/><path d="M2,23 L12,12" stroke="var(--teal)" stroke-width="1.5"/></svg>
      Increase building value
    </h2>
    <p>Help owners/investors increase their ROI on their apartments by providing bulk high speed internet services that’s delivered through a state of the art HD WIFI system designed for your building</p>
  </section>

  <footer class="contact">
    <h2 class="contact-heading">GET IN TOUCH</h2>
    <p class="contact-lines">PO BOX 1180<br>Brisbane QLD 4000<br>Phone 1300 555 014<br>Fax 1300 555 015</p>
    <p class="contact-web">hello@skylinkwifi.com.au<br>www.skylinkwifi.com.au</p>
  </footer>
</div>
</body>
</html>
```